Vantro cards

I am in the auto motive, transportation business I would like a business card that is Something cool, modern edgy, having to do with car culture. I offer towing service for high and exotic cars. I also provide towing for collisions and car accidents. I offer open and enclosed transport nationwide.

Target Market(s)

Car culture people high end auto collectors

Industry/Entity Type

Towing car carrier

Contact Information for Business Card

My company colors black yellow and silver

Font styles to use
Serif

```html
<!DOCTYPE html>
<html lang="en">
<head>
<meta charset="utf-8">
<title>Vantro Transportation — Business Cards</title>
<link href="https://fonts.googleapis.com/css2?family=Poppins:wght@400;500;600;700;800&display=swap" rel="stylesheet">
<style>
  :root {
    --backdrop: #959394;
    --card-white: #ffffff;
    --ink: #050505;
    --brand-yellow: #fadf5e;
    --shadow: #1c1c1c;
  }
  * { margin: 0; padding: 0; box-sizing: border-box; }
  html, body { width: 1075px; height: 1200px; overflow: hidden; }
  body {
    background: var(--backdrop);
    font-family: "Poppins", sans-serif;
    position: relative;
  }
  .card {
    position: absolute;
    left: 206px;
    width: 663px;
    height: 395px;
    overflow: hidden;
    box-shadow: 3px 3px 0 var(--shadow), 4px 4px 4px rgba(0,0,0,.35);
  }
  .card--front { top: 187px; background: var(--card-white); }
  .card--back { top: 637px; background: var(--ink); }

  /* front */
  .wordmark {
    position: absolute;
    display: flex;
    flex-direction: column;
    align-items: center;
    gap: 12px;
    font-weight: 800;
    letter-spacing: 2px;
  }
  .wordmark__square {
    width: 54px; height: 54px;
    background: var(--brand-yellow);
  }
  .card--front .wordmark {
    left: 515px; top: 62px;
    transform: translateX(-50%);
    color: var(--ink);
    font-size: 44px; line-height: 1;
  }
  .holder {
    position: absolute; left: 35px; top: 222px;
  }
  .holder__name {
    font-size: 22px; font-weight: 600; color: var(--ink); line-height: 1.1;
  }
  .holder__role {
    font-size: 18px; font-weight: 400; color: #222; line-height: 1.2;
  }
  .holder__rule {
    position: absolute; left: 35px; top: 277px;
    width: 210px; height: 5px; background: var(--brand-yellow);
  }
  .contact-band {
    position: absolute; left: 0; top: 279px;
    width: 100%; height: 116px; background: var(--ink);
    color: var(--card-white);
  }
  .contact-list {
    list-style: none;
    position: absolute; left: 35px; top: 20px;
    font-size: 19px; line-height: 23.5px;
  }
  .contact-list li { display: flex; align-items: center; gap: 6px; }
  .contact-list svg { width: 18px; height: 18px; flex: none; }
  .address {
    position: absolute; right: 40px; top: 47px;
    text-align: right; font-size: 19px; line-height: 23.5px; font-style: normal;
  }

  /* back */
  .card--back .wordmark {
    left: 331px; top: 120px;
    transform: translateX(-50%);
    color: var(--card-white);
    font-size: 50px; line-height: 1;
  }
  .web-band {
    position: absolute; left: 0; top: 350px;
    width: 100%; height: 45px; background: var(--brand-yellow);
    color: var(--card-white);
    font-size: 19px; text-align: center; line-height: 45px;
  }
</style>
</head>
<body>

<section class="card card--front" aria-label="Card front">
  <div class="wordmark">
    <span class="wordmark__square"></span>
    <span class="wordmark__name">VANTRO</span>
  </div>

  <div class="holder">
    <p class="holder__name">MARCUS HALE</p>
    <p class="holder__role">Managing Director</p>
  </div>
  <span class="holder__rule"></span>

  <div class="contact-band">
    <ul class="contact-list">
      <li>
        <svg viewBox="0 0 24 24" aria-hidden="true"><path fill="#fadf5e" d="M6.6 10.8a15.1 15.1 0 0 0 6.6 6.6l2.2-2.2a1 1 0 0 1 1-.25 11.4 11.4 0 0 0 3.6.57 1 1 0 0 1 1 1V20a1 1 0 0 1-1 1A17 17 0 0 1 3 4a1 1 0 0 1 1-1h3.5a1 1 0 0 1 1 1c0 1.25.2 2.45.57 3.57a1 1 0 0 1-.25 1z"/></svg>
        044-555 018 273
      </li>
      <li>
        <svg viewBox="0 0 24 24" aria-hidden="true"><rect x="2" y="5" width="20" height="14" fill="#fadf5e"/><path d="M2 5l10 8 10-8" fill="none" stroke="#050505" stroke-width="1.6"/></svg>
        info@vantrotow.com
      </li>
      <li>
        <svg viewBox="0 0 24 24" aria-hidden="true"><g fill="none" stroke="#fadf5e" stroke-width="2"><circle cx="12" cy="12" r="9"/><ellipse cx="12" cy="12" rx="4" ry="9"/><path d="M3 12h18M5 7h14M5 17h14"/></g></svg>
        www.vantrotow.com
      </li>
    </ul>
    <address class="address">
      421, Address line goes here<br>45452,Country Name
    </address>
  </div>
</section>

<section class="card card--back" aria-label="Card back">
  <div class="wordmark">
    <span class="wordmark__square"></span>
    <span class="wordmark__name">VANTRO</span>
  </div>
  <div class="web-band">www.vantrotow.com</div>
</section>

</body>
</html>
```